AMBER AND SLATE WEB

We need a home design in wordpress, we have now a web but we would like to improve it. Our current web is www.amberandslatevillas.example Our business is holliday rental of villas in Ibiza. Our guest must know that we are a reliable company, professional and with experience and good reviews. We want them to click in our reservation engine: https://bookings.amberandslatevillas.example/en/ and make reservation in our website. We would also like to say that all the properties that we have are just us who commercialize so we have best price available. Many people are going to see our villas in staylist.example and look to our website to make a reservation with us so we need to show them that they are at the right place and click at our link to our reservation engine. What make us special is that we are a local company, we are from Ibiza, Our guests are always received in person by the Amber and Slate Ibiza team. You will enjoy extensive tourist information when you check in and during the entire stay. You will be attended by ChatterLine and calls, always happy to help so that you have a happy and fun stay! Our guest stay is better than in hotel as they have more spece, private swiming pool, private garden, barbeque ... To rent a villa is the best way to stay in Ibiza. We also have a promotional video: https://vidshare.example/Qm7TzR2pLxA Let our philosophy be shown, we think that coming on holiday to Ibiza implies seeing the nature that we have in Ibiza, hence our name AMBER AND SLATE, like the pins that almost touch the sea in Ibiza, or the posidonea meadows where the intense green of the seaweed and the blue of the sea. We are aware of the environment, and we love Ibiza. For us, the client who visits Ibiza, should rent a car, go around the island, eat in a restaurant one day in front of the sea, is a night of partying to the discs, go shopping, visit the ancient heritage of Umanity, make some aquatic sport, enjoy the pool, those are for us Ibiza.

Target Market(s)

Europe, people from Holand, UK, Germany, France, Spain ...

Industry/Entity Type

Tourism

Colors

Designer to choose colors to be used in the design.

Requirements
Must have
• Pictures of Ibiza.
Nice to have
• Our name Amber and Slate Ibiza is beacuse in Ibiza there is forest that almost touch the watter of the Mediterranean sea, so you can see green of the forest and blue of the sea and the sky. And also beacause under the watter of the sea there is a plant called Posidonia that is also green please see the picture of posidonia.

```html
<!DOCTYPE html>
<html lang="en">
<head>
<meta charset="utf-8">
<title>Amber and Slate Villas Ibiza</title>
<link href="https://fonts.googleapis.com/css2?family=Cormorant+Garamond:wght@400;500;600&family=Montserrat:wght@400;500;600;700;800;900&display=swap" rel="stylesheet">
<style>
:root{
  --green:#95c13d;
  --green-dark:#3f6f4f;
  --teal:#2b8796;
  --text:#5d6266;
  --muted:#8a8f93;
  --ghost:#f1f2f2;
  --line:#e4e6e7;
  --white:#ffffff;
  --sea:#1f86c4;
}
*{margin:0;padding:0;box-sizing:border-box}
html,body{width:1200px;height:4651px;overflow:hidden;background:var(--white)}
body{position:relative;font-family:'Montserrat',sans-serif;color:var(--text)}
.abs{position:absolute}
.photo{position:absolute}

/* header */
.site-header{position:absolute;left:0;top:0;width:1200px;height:83px;background:var(--white)}
.brand{position:absolute;display:flex;align-items:center;gap:10px;color:var(--green-dark);font-family:'Cormorant Garamond',serif;font-weight:500;letter-spacing:.5px;white-space:nowrap}
.brand-dot{width:22px;height:22px;border-radius:50%;background:var(--green)}
.site-header .brand{left:152px;top:28px;font-size:19px}
.lang{position:absolute;display:flex;align-items:center;gap:6px;font-size:10px;color:var(--muted);font-weight:500}
.flag{width:16px;height:11px;background:repeating-linear-gradient(#c8323c 0 1.6px,#fff 1.6px 3.2px);position:relative}
.flag::before{content:"";position:absolute;left:0;top:0;width:7px;height:6px;background:#2d3f86}
.main-nav{position:absolute;left:500px;top:35px;display:flex;gap:32px;font-size:10px;font-weight:500;letter-spacing:.4px;color:#444;white-space:nowrap}
.main-nav .active{color:var(--green)}
.btn{display:inline-flex;align-items:center;justify-content:center;background:var(--green);color:var(--white);font-weight:700;font-size:11px;letter-spacing:1px;box-shadow:0 4px 10px rgba(0,0,0,.15)}
.book-btn{position:absolute;left:966px;top:23px;width:86px;height:37px;font-size:10px}

/* hero */
.hero{position:absolute;left:0;top:83px;width:1200px;height:621px;background:linear-gradient(180deg,#2f78c4 0%,#2a8ccc 50%,#4fb0cc 100%)}
.hero-kicker{position:absolute;left:0;width:1200px;top:128px;text-align:center;font-family:'Cormorant Garamond',serif;font-size:25px;letter-spacing:9px;color:var(--white)}
.hero-title{position:absolute;left:0;width:1200px;top:150px;text-align:center;font-weight:900;font-size:150px;letter-spacing:4px;color:var(--white);line-height:1}
.booking-bar{position:absolute;left:152px;top:408px;width:900px;height:105px;background:var(--white);box-shadow:0 8px 24px rgba(0,0,0,.18);display:flex;align-items:center;padding:0 26px 0 34px}
.field{position:relative;height:64px;padding-top:12px;border-right:1px solid var(--line)}
.field-label{font-size:9px;letter-spacing:.6px;color:#666;font-weight:500}
.field-value{margin-top:10px;font-family:'Cormorant Garamond',serif;font-size:30px;font-weight:600;color:#222}
.field-value small{font-size:15px;font-weight:500;margin-left:6px}
.caret{position:absolute;right:16px;top:38px;border:3.5px solid transparent;border-top:4px solid #666}
.reserve-btn{width:165px;height:57px;margin-left:auto}

/* ghost words */
.ghost{position:absolute;font-family:'Cormorant Garamond',serif;color:var(--ghost);letter-spacing:22px;line-height:1;white-space:nowrap;font-weight:400}

.section-title{position:absolute;font-family:'Cormorant Garamond',serif;font-weight:500;color:var(--green-dark);letter-spacing:6px;line-height:1.2}
.copy{position:absolute;font-size:12.5px;line-height:24px;color:var(--text)}
.link{position:absolute;font-size:10px;font-weight:600;letter-spacing:.5px;color:var(--teal);text-decoration:underline}

/* special list */
.perks{position:absolute;left:700px;top:3028px;width:360px;list-style:none}
.perks li{display:flex;gap:18px;font-size:12px;line-height:22px;color:var(--text);margin-bottom:22px}
.perks svg{flex:none;width:32px;height:32px;stroke:var(--teal);fill:none;stroke-width:1.5}

/* testimonials */
.stars{position:absolute;left:248px;top:3730px;font-size:12px;color:#f0962a;letter-spacing:1px}
.stars span{color:var(--teal);font-weight:600;margin-left:6px;letter-spacing:0}
.quote{position:absolute;left:248px;top:3778px;width:730px;font-size:16px;line-height:30px;color:#333}
.arrow{position:absolute;width:40px;height:40px;border-radius:50%;display:flex;align-items:center;justify-content:center}
.arrow-prev{left:150px;top:3829px;border:1.5px solid var(--green)}
.arrow-next{left:1010px;top:3829px;background:var(--green)}
.avatar{position:absolute;left:248px;top:3898px;width:56px;height:56px;border-radius:50%;background:linear-gradient(135deg,#c9ccd0,#8b9096)}
.author{position:absolute;left:326px;top:3903px}
.author-name{font-family:'Cormorant Garamond',serif;font-weight:600;font-size:15px;letter-spacing:1.5px;color:#333}
.author-meta{font-size:11px;color:var(--muted);margin-top:6px}

/* footer */
.site-footer .brand{left:152px;top:4388px;font-size:26px}
.footer-info{position:absolute;left:152px;top:4502px;font-size:11px;line-height:16px;color:var(--text)}
.footer-nav{position:absolute;left:640px;top:4394px;list-style:none;font-size:10px;font-weight:600;letter-spacing:.5px;color:#333}
.footer-nav li{height:38px}
.copyright{position:absolute;right:148px;top:4587px;font-size:10px;color:var(--muted)}
</style>
</head>
<body>

<header class="site-header">
  <div class="brand"><span class="brand-dot"></span>AMBER AND SLATE</div>
  <div class="lang" style="left:396px;top:36px"><span class="flag"></span>EN ▾</div>
  <nav class="main-nav">
    <span class="active">HOME</span><span>EXPERIENCE</span><span>ABOUT US</span><span>CONTACT US</span><span>ALL PROPERTIES</span>
  </nav>
  <a class="btn book-btn">BOOK</a>
</header>

<section class="hero" role="img" aria-label="Photo of an Ibiza cove with turquoise water, pine covered cliffs and sailing boats">
  <div class="hero-kicker">THE BEST WAY TO STAY IN</div>
  <div class="hero-title">IBIZA</div>
  <form class="booking-bar">
    <div class="field" style="width:166px"><div class="field-label">CHECK-IN</div><div class="field-value">19<small>May</small></div><i class="caret"></i></div>
    <div class="field" style="width:166px;padding-left:22px"><div class="field-label">CHECK-OUT</div><div class="field-value">02<small>June</small></div><i class="caret"></i></div>
    <div class="field" style="width:118px;padding-left:22px"><div class="field-label">ROOMS</div><div class="field-value">02</div><i class="caret"></i></div>
    <div class="field" style="width:118px;padding-left:22px"><div class="field-label">ADULTS</div><div class="field-value">03</div><i class="caret"></i></div>
    <div class="field" style="width:90px;padding-left:22px;border-right:none"><div class="field-label">CHILDREN</div><div class="field-value">01</div><i class="caret" style="right:6px"></i></div>
    <a class="btn reserve-btn">RESERVE</a>
  </form>
</section>

<section class="villas">
  <div class="ghost" style="left:48px;top:808px;font-size:118px">VILLAS</div>
  <h2 class="section-title" style="left:152px;top:852px;font-size:36px">VILLAS &amp;<br>THE COUNTRYSIDE</h2>
  <p class="copy" style="left:152px;top:958px;width:412px">Amber and Slate Villas Ibiza is a company specialized in offering its clients accommodation in Villas on the countryside of Ibiza. Our guests enjoy the rural Ibiza, tranquility, relax, private pool, close to dream beaches and coves, the best restaurants, an unforgettable holiday for family or friends.</p>
  <a class="link" style="left:152px;top:1104px">VIEW ALL PROPERTIES</a>
  <div class="photo" style="left:630px;top:841px;width:204px;height:134px;background:linear-gradient(135deg,#7f9a5a,#b58a5e)" role="img" aria-label="Villa terrace with breakfast table"></div>
  <div class="photo" style="left:630px;top:991px;width:204px;height:134px;background:linear-gradient(135deg,#d9cbb8,#8a6a4e)" role="img" aria-label="Bright villa living room"></div>
  <div class="photo" style="left:848px;top:841px;width:204px;height:284px;background:linear-gradient(180deg,#2a7fc9,#4cb3d6)" role="img" aria-label="White villa with private swimming pool"></div>
</section>

<section class="experience">
  <div class="ghost" style="left:596px;top:1262px;font-size:118px">EXPERIENCE</div>
  <div class="photo" style="left:152px;top:1245px;width:202px;height:284px;background:linear-gradient(180deg,#3a8fd2,#8a8a6a)" role="img" aria-label="Wooden jetty over clear sea water"></div>
  <div class="photo" style="left:368px;top:1245px;width:203px;height:134px;background:linear-gradient(180deg,#4aa8cc,#cdbf9e)" role="img" aria-label="Kayaks on a sandy beach"></div>
  <div class="photo" style="left:368px;top:1395px;width:203px;height:134px;background:linear-gradient(180deg,#3b93d8,#146bb2)" role="img" aria-label="Boat trip towards a rocky islet"></div>
  <p class="copy" style="left:630px;top:1340px;width:410px">Every day can be a different experience, beach, restaurant, flea market, disco, hiking, kayaking, horseback riding, shopping, history, boat ride! There is a lot of variety for all budgets!</p>
  <a class="link" style="left:630px;top:1441px">CONTACT US TO LEARN MORE</a>
</section>

<section class="freedom">
  <div class="ghost" style="left:48px;top:1672px;font-size:118px">FREEDOM</div>
  <div class="photo" style="left:565px;top:1622px;width:570px;height:456px;background:linear-gradient(180deg,#f4f5f5,#eeefef)" role="img" aria-label="Faint outline map of the island of Ibiza"></div>
  <p class="copy" style="left:152px;top:1749px;width:410px">The maximum distances of the island are 41 kilometers from north to south and 15 kilometers from east to west, we always recommend renting a car. Enjoy the freedom to go where you prefer, without depending on schedules or public transportation.</p>
  <a class="link" style="left:152px;top:1872px">CONTACT US TO LEARN MORE</a>
  <div class="photo" style="left:630px;top:1648px;width:204px;height:284px;background:linear-gradient(180deg,#9fbf8a,#3d5f8e)" role="img" aria-label="Friends driving an open-top off-road car"></div>
</section>

<section class="video">
  <div class="photo" style="left:152px;top:2144px;width:900px;height:506px;background:linear-gradient(160deg,#9cc3de 0%,#7d9a5a 55%,#4a4232 100%);box-shadow:0 18px 36px rgba(0,0,0,.22)" role="img" aria-label="Promotional video still of a villa porch with guests dining among palm trees"></div>
  <div class="abs" style="left:560px;top:2357px;width:80px;height:80px;border-radius:50%;background:rgba(255,255,255,.9);display:flex;align-items:center;justify-content:center">
    <svg width="22" height="24" viewBox="0 0 22 24"><path d="M2 1l19 11L2 23z" fill="#95c13d"/></svg>
  </div>
</section>

<section class="special">
  <div class="ghost" style="left:278px;top:2770px;font-size:118px">SPECIAL</div>
  <h2 class="section-title" style="left:0;width:1200px;text-align:center;top:2838px;font-size:36px">WHAT MAKES US SPECIAL</h2>
  <p class="copy" style="left:0;width:1200px;text-align:center;top:2902px;font-size:11.5px;line-height:22px">Our guest stay better than in a hotel as they have more spece, private swirning<br>pool, private garden, barbeque... To rent a villa is the best way to stay in Ibiza.</p>
  <div class="photo" style="left:152px;top:3023px;width:456px;height:313px;background:linear-gradient(180deg,#5c9fd4,#1a8fc8)" role="img" aria-label="Villa pool with sun loungers and parasol"></div>
  <ul class="perks">
    <li><svg viewBox="0 0 32 32"><path d="M16 4a7 7 0 017 7c0 6-7 12-7 12S9 17 9 11a7 7 0 017-7z"/><circle cx="16" cy="11" r="2.5"/><path d="M5 28l4-7h14l4 7z"/></svg><span>We are a local company, we are from Ibiza</span></li>
    <li><svg viewBox="0 0 32 32"><circle cx="16" cy="9" r="5"/><path d="M7 29v-6a9 9 0 0118 0v6"/><path d="M16 18v6"/></svg><span>Our guests are always received in person by the Amber and Slate Ibiza team</span></li>
    <li><svg viewBox="0 0 32 32"><rect x="7" y="5" width="18" height="24" rx="2"/><path d="M12 5V3h8v2M11 13h2M15 13h7M11 19h2M15 19h7M11 24h2M15 24h7"/></svg><span>You will enjoy extensive tourist information when you check in and during the entire stay</span></li>
    <li><svg viewBox="0 0 32 32"><rect x="9" y="3" width="14" height="26" rx="2"/><path d="M14 25h4M13 12c2 3 4 4 6 4"/></svg><span>You will be attended by ChatterLine and calls, always happy to help so that you have a happy</span></li>
  </ul>
  <a class="btn abs" style="left:711px;top:3289px;width:164px;height:48px">RESERVE</a>
</section>

<section class="testimonials">
  <div class="ghost" style="left:8px;top:3468px;font-size:118px">TESTIMONIALS</div>
  <h2 class="section-title" style="left:0;width:1200px;text-align:center;top:3527px;font-size:36px">TESTIMONIALS</h2>
  <p class="copy" style="left:0;width:1200px;text-align:center;top:3590px;font-size:11.5px;line-height:23px">Each client is different, both for those who discover Ibiza for the first time and for those who<br>have already been many times, it is a pleasure for us to share our favorite places with our<br>guests and help them to make their experience very special.</p>
  <div class="stars">★★★★★<span>Villa Can Roure</span></div>
  <p class="quote">“Nullam ut semper mauris, ut tristique odio. Nulla vestibulum pellentesqu tincidunt.<br>Mauris pulvinar et neque eget ipsum malesuada aliquamter. Duis condimen a tum<br>feugiat quam quis mollis. Etiam tristique faucibus leo non elementum.”</p>
  <div class="arrow arrow-prev"><svg width="14" height="10" viewBox="0 0 14 10"><path d="M13 5H1M5 1L1 5l4 4" stroke="#95c13d" fill="none" stroke-width="1.4"/></svg></div>
  <div class="arrow arrow-next"><svg width="14" height="10" viewBox="0 0 14 10"><path d="M1 5h12M9 1l4 4-4 4" stroke="#fff" fill="none" stroke-width="1.4"/></svg></div>
  <div class="avatar" role="img" aria-label="Guest portrait"></div>
  <div class="author"><div class="author-name">JOHN DOE</div><div class="author-meta">Desde Barcelona, Spain - September 2019</div></div>
  <a class="btn abs" style="left:496px;top:4016px;width:210px;height:49px">VIEW ALL REVIEWS</a>
</section>

<div class="photo" style="left:0;top:4160px;width:1200px;height:166px;background:linear-gradient(180deg,#7d9a6a 0%,#a08a6a 55%,#2a8fc8 100%)" role="img" aria-label="Pine forest meeting the sea along an Ibiza coastline"></div>

<footer class="site-footer">
  <div class="brand"><span class="brand-dot" style="width:30px;height:30px"></span>AMBER AND SLATE</div>
  <div class="footer-info">
    CALLE DEL PINAR, 8,<br>SANTA EULARIA DES RIU, 07840, IBIZA, Spain
    <div style="margin-top:14px">Phone: <b style="color:#333">+34600123456</b></div>
    <div style="margin-top:13px">Email: <b style="color:#333">reservas@amberandslatevillas.example</b></div>
  </div>
  <ul class="footer-nav">
    <li>HOME</li><li>EXPERIENCE</li><li>ABOUT US</li><li>CONTACT US</li><li>ALL PROPERTIES</li><li>BOOK</li>
  </ul>
  <div class="lang" style="left:1005px;top:4399px"><span class="flag" style="width:22px;height:15px"></span>EN</div>
  <div class="copyright">©2019 All rights reserved</div>
</footer>

</body>
</html>
```